Calloway needs a modernized design

We would like a modern update (that can be responsive) to our existing website. Attached are the two existing pages we would like new concepts of - our home page and a page about one of our locations.

Calloway is provides executive offices and virtual office services. Startups, law firms, and financial services are our primary clients. We would like a professional, clean design, leaning towards minimalist. We intend to greatly reduce/eliminate the long paragraphs of text.

Requirements
Must have
• A design that can be responsive
Nice to have
• Large image(s) on home page that rotate.

```html
<!DOCTYPE html>
<html lang="en">
<head>
<meta charset="utf-8">
<title>Calloway Business Centers</title>
<link href="https://fonts.googleapis.com/css2?family=Bitter:wght@400;700&family=Ubuntu:wght@400;500;700&family=Arimo:wght@400;700&family=Open+Sans:wght@300;400&display=swap" rel="stylesheet">
<style>
:root{
  --navy:#1f3466;
  --navy-deep:#17294f;
  --blue:#3a8fc7;
  --band:#555555;
  --ink:#222222;
  --muted:#666666;
  --light:#ececec;
  --footer:#222222;
  --footer-deep:#141414;
  --yellow:#f7d61a;
  --white:#ffffff;
}
*{box-sizing:border-box;margin:0;padding:0}
html,body{width:1200px;height:3025px;overflow:hidden}
body{position:relative;background:var(--white);font-family:"Arimo",Arial,sans-serif;color:var(--ink)}
.abs{position:absolute}
.slab{font-family:"Bitter",Georgia,serif}

/* header */
.site-header{left:0;top:0;width:1200px;height:100px;background:var(--white)}
.brand{left:48px;top:14px;display:flex;align-items:center;gap:12px}
.brand-dot{width:72px;height:72px;border-radius:50%;background:var(--navy)}
.brand-name{font-family:"Bitter",Georgia,serif;font-weight:700;font-size:34px;color:var(--navy);letter-spacing:1px}
.contact{display:flex;align-items:center;gap:12px;font-size:14px;line-height:20px;color:#333}
.contact svg{flex:none}

/* nav */
.main-nav{left:0;top:100px;width:1200px;height:50px;background:var(--navy)}
.main-nav a{position:absolute;top:17px;color:var(--white);text-decoration:none;font-family:"Bitter",Georgia,serif;font-size:13px;letter-spacing:.5px}
.social-dot{position:absolute;top:13px;width:24px;height:24px;border-radius:50%;background:#7a7f8c}

/* hero */
.hero{left:0;top:150px;width:1200px;height:542px;background:linear-gradient(100deg,#eef1f3 0%,#dfe5ea 35%,#c9cfd6 55%,#e9ecef 80%,#f5f6f7 100%)}
.hero-card{left:48px;top:306px;width:398px;height:138px;background:rgba(255,255,255,.88);border-left:8px solid var(--navy);padding:22px 0 0 28px}
.hero-card .kicker{font-family:"Ubuntu",sans-serif;font-size:28px;color:#333;letter-spacing:.5px}
.hero-card .headline{font-family:"Ubuntu",sans-serif;font-weight:700;font-size:48px;color:var(--navy);line-height:54px}
.btn-navy{background:var(--navy);color:var(--white);font-family:"Ubuntu",sans-serif;font-size:15px;display:flex;align-items:center;justify-content:center;gap:8px}
.hero .btn-navy{position:absolute;left:105px;top:276px;width:128px;height:44px}

.quote-band{left:0;top:692px;width:1200px;height:56px;background:var(--band)}
.quote-band p{position:absolute;left:58px;top:16px;color:var(--white);font-family:"Ubuntu",sans-serif;font-weight:500;font-size:20px}
.quote-band .btn-navy{position:absolute;left:970px;top:10px;width:143px;height:42px}

/* features */
.feature{width:245px}
.feature-photo{width:245px;height:172px}
.feature h3{font-family:"Bitter",Georgia,serif;font-weight:700;font-size:23px;color:var(--ink);margin:18px 0 6px}
.feature p{font-size:13.5px;line-height:20px;color:#333}
.what-box{left:891px;top:780px;width:253px;height:316px;border:4px solid var(--navy);padding:14px 20px}
.what-box h2{font-family:"Bitter",Georgia,serif;font-weight:700;font-size:29px;line-height:34px;color:var(--navy)}
.what-box .rule{width:30px;height:3px;background:var(--navy);margin:8px 0 24px}
.what-box p{font-size:13.5px;line-height:20px;color:#333}
.what-box .more{margin-top:28px;font-size:13px;color:#222}

/* services */
.services{left:0;top:1166px;width:1200px;height:206px;background:var(--navy)}
.service{position:absolute;top:40px;width:200px;text-align:center;color:var(--white)}
.service svg{display:block;margin:0 auto 18px}
.service span{font-family:"Bitter",Georgia,serif;font-weight:700;font-size:17px;line-height:22px}

/* news */
.section-title{width:1200px;text-align:center;font-family:"Bitter",Georgia,serif;font-size:30px;color:#333;letter-spacing:1px}
.title-rule{width:200px;height:1px;background:#bbb;left:500px}
.news-icon{width:92px;height:92px;border-radius:50%;border:6px solid var(--blue);display:flex;align-items:center;justify-content:center}
.view-btn{width:94px;height:34px;border:1px solid #999;font-size:13px;color:#333;display:flex;align-items:center;justify-content:center}
.news-title{font-family:"Bitter",Georgia,serif;font-size:22px;color:#333}
.news-meta{font-size:11px;color:#888;font-weight:700;display:flex;gap:22px}
.news-body{width:528px;font-size:13.5px;line-height:21px;color:#444}
.news-photo{width:327px;height:167px}
.news-divider{left:48px;top:1698px;width:1080px;height:1px;background:#ddd}

/* video */
.watch{left:0;top:1940px;width:1200px;height:468px;background:var(--light)}
.video{left:329px;top:2051px;width:546px;height:323px;background:linear-gradient(180deg,#4a4a58 0%,#8f7f78 40%,#e4d8c4 52%,#3b3c40 70%,#1c1d22 100%)}
.video-title{left:16px;top:12px;color:var(--white);font-size:16px}
.play{left:243px;top:131px;width:60px;height:60px;border-radius:50%;background:rgba(0,0,0,.6);display:flex;align-items:center;justify-content:center}
.video-bar{left:0;top:283px;width:546px;height:40px;background:rgba(0,0,0,.75);display:flex;align-items:center;gap:14px;padding:0 14px;color:var(--white);font-size:12px}

/* contact */
.touch{left:0;top:2408px;width:1200px;height:325px;background:linear-gradient(110deg,#101f45 0%,#1b3163 45%,#2a4a82 75%,#4f6a98 100%)}
.touch h2{position:absolute;top:58px;width:1200px;text-align:center;font-family:"Bitter",Georgia,serif;font-weight:700;font-size:38px;color:var(--white);letter-spacing:1px}
.touch .rule{left:500px;top:118px;width:200px;height:1px;background:rgba(255,255,255,.5)}
.touch p{position:absolute;top:136px;width:1200px;text-align:center;font-size:20px;color:var(--white)}
.field{top:208px;height:46px;background:var(--white);font-size:14px;color:#555;padding:15px 14px}
.subscribe{left:964px;top:208px;width:135px;height:46px;background:var(--yellow);font-family:"Ubuntu",sans-serif;font-weight:500;font-size:16px;color:#111;display:flex;align-items:center;justify-content:center}

/* footer */
.site-footer{left:0;top:2733px;width:1200px;height:242px;background:var(--footer);color:var(--white)}
.site-footer h4{position:absolute;top:40px;font-family:"Open Sans",sans-serif;font-weight:300;font-size:23px}
.foot-links{position:absolute;top:92px;list-style:none;font-size:14px;line-height:27px}
.news-box{left:494px;top:80px;width:256px;height:146px;background:#2b2b2b;padding:0 0 0 0}
.news-box .lead{font-family:"Open Sans",sans-serif;font-size:16px;color:#ccc;padding:0 0 0 0}
.news-box .small{font-size:13px;line-height:19px;color:#ddd;margin-top:12px}
.mail-row{position:absolute;left:0;top:108px;width:256px;height:32px;display:flex}
.mail-row span{display:flex;align-items:center;font-size:13px}
.mail-in{width:172px;background:var(--white);color:#777;padding-left:10px}
.mail-btn{flex:1;background:#f1f1f1;color:#999;justify-content:center}
.foot-social{position:absolute;top:80px;width:40px;height:40px;border-radius:50%}
.foot-brand{left:889px;top:172px;display:flex;align-items:center;gap:10px}
.foot-brand .brand-dot{width:56px;height:56px;background:#bbb}
.foot-brand .brand-name{color:#ccc;font-size:28px}
.copyright{left:0;top:2975px;width:1200px;height:50px;background:var(--footer-deep);color:#ccc;font-size:11px;text-align:center;line-height:50px}
</style>
</head>
<body>

<header class="site-header abs">
  <div class="brand abs"><span class="brand-dot"></span><span class="brand-name">CALLOWAY</span></div>
  <div class="contact abs" style="left:716px;top:30px">
    <svg width="36" height="36" viewBox="0 0 36 36"><circle cx="18" cy="18" r="16" fill="none" stroke="#1f3466" stroke-width="2.5"/><path d="M12 11c1-1 2.5-1 3 0l1.5 3c.4.8 0 1.6-.6 2l-1 .8c.8 2 2.4 3.6 4.4 4.4l.8-1c.4-.6 1.2-1 2-.6l3 1.5c1 .5 1 2 0 3-2 2-5 2-9-1.5S10 13 12 11z" fill="#1f3466"/></svg>
    <div>001 480 2271<br>hello@callowayoffices.example</div>
  </div>
  <div class="contact abs" style="left:984px;top:30px">
    <svg width="22" height="36" viewBox="0 0 22 36"><path d="M11 2C5.5 2 2 6 2 11c0 7 9 19 9 19s9-12 9-19c0-5-3.5-9-9-9z" fill="#1f3466"/><circle cx="11" cy="11" r="3.5" fill="#fff"/></svg>
    <div>Harbourview House,<br>Kelso Park Ind Est.</div>
  </div>
</header>

<nav class="main-nav abs">
  <a style="left:65px">HOME</a>
  <a style="left:155px">PROPERTIES</a>
  <a style="left:286px">VIRTUAL TOURS &amp; VIDEOS</a>
  <a style="left:514px">PHOTOS</a>
  <a style="left:617px">BROKER REFERRALS</a>
  <span class="social-dot" style="left:992px"></span>
  <span class="social-dot" style="left:1023px"></span>
  <span class="social-dot" style="left:1054px"></span>
  <span class="social-dot" style="left:1085px"></span>
  <span class="social-dot" style="left:1116px"></span>
</nav>

<section class="hero abs" role="img" aria-label="Two business colleagues reviewing a laptop in a bright office">
  <div class="hero-card abs" style="left:48px;top:156px">
    <div class="kicker">EXECUTIVE OFFICE SUITES</div>
    <div class="headline">ON LOW COST</div>
  </div>
  <div class="btn-navy">Learn More <svg width="8" height="12" viewBox="0 0 8 12"><path d="M1 1l5 5-5 5" fill="none" stroke="#fff" stroke-width="2"/></svg></div>
</section>

<section class="quote-band abs">
  <p>Looking for a First-Class Business Plan Consultant?</p>
  <div class="btn-navy">Get a Quote <svg width="8" height="12" viewBox="0 0 8 12"><path d="M1 1l5 5-5 5" fill="none" stroke="#fff" stroke-width="2"/></svg></div>
</section>

<article class="feature abs" style="left:48px;top:780px">
  <div class="feature-photo" role="img" aria-label="Smartphone showing a target with a dart" style="background:linear-gradient(135deg,#d9dadc,#9ea3a8 55%,#5e6570)"></div>
  <h3>Value</h3>
  <p>Nulla facilisi. Suspendisse hendrerit purus blandit feugiat ornare. In varius lectus sit amet sem tempor, sit amet mattis dolor ultrices.</p>
</article>
<article class="feature abs" style="left:323px;top:780px">
  <div class="feature-photo" role="img" aria-label="Modern glass office building" style="background:linear-gradient(135deg,#eceff1,#b9c2c8 50%,#6f7a82)"></div>
  <h3>Community</h3>
  <p>Nulla facilisi. Suspendisse hendrerit purus blandit feugiat ornare. In varius lectus sit amet sem tempor, sit amet mattis dolor ultrices.</p>
</article>
<article class="feature abs" style="left:597px;top:780px">
  <div class="feature-photo" role="img" aria-label="Team working together at a desk" style="background:linear-gradient(135deg,#f3f3f3,#b7b2ad 50%,#4c4a4c)"></div>
  <h3>Service</h3>
  <p>Nulla facilisi. Suspendisse hendrerit purus blandit feugiat ornare. In varius lectus sit amet sem tempor, sit amet mattis dolor ultrices.</p>
</article>
<aside class="what-box abs">
  <h2>what we do<br>for you</h2>
  <div class="rule"></div>
  <p>Nulla facilisi. Suspendisse hendrerit purus blandit feugiat ornare. In varius lectus sit amet sem tempor, sit amet mattis dolor ultrices.Nulla facilisi. Suspendisse hendrerit purus blandit feugiat ornare.</p>
  <div class="more">Learn More &rsaquo;</div>
</aside>

<section class="services abs">
  <div class="service" style="left:29px">
    <svg width="50" height="52" viewBox="0 0 50 52"><circle cx="25" cy="13" r="11" fill="#fff"/><path d="M5 50c0-14 9-22 20-22s20 8 20 22z" fill="#fff"/></svg>
    <span>Executive Office<br>Suites</span>
  </div>
  <div class="service" style="left:261px">
    <svg width="60" height="52" viewBox="0 0 60 52"><circle cx="30" cy="12" r="8" fill="#fff"/><circle cx="13" cy="16" r="6" fill="#fff"/><circle cx="47" cy="16" r="6" fill="#fff"/><path d="M18 50c0-18 6-26 12-26s12 8 12 26z" fill="#fff"/><path d="M3 46c0-14 5-20 10-20s9 5 9 12v8zM57 46c0-14-5-20-10-20s-9 5-9 12v8z" fill="#fff"/></svg>
    <span>On-demand<br>Meeting Rooms</span>
  </div>
  <div class="service" style="left:497px">
    <svg width="56" height="52" viewBox="0 0 56 52"><rect x="4" y="3" width="48" height="32" fill="none" stroke="#fff" stroke-width="3"/><circle cx="16" cy="24" r="5" fill="#fff"/><path d="M8 50c0-10 3-16 8-16s8 6 8 16z" fill="#fff"/><path d="M24 14h20M24 20h14" stroke="#fff" stroke-width="3"/></svg>
    <span>On-demand<br>Training Rooms</span>
  </div>
  <div class="service" style="left:731px">
    <svg width="56" height="52" viewBox="0 0 56 52"><circle cx="20" cy="20" r="8" fill="#fff"/><path d="M6 50c0-14 6-20 14-20s14 6 14 20z" fill="#fff"/><rect x="34" y="2" width="18" height="26" rx="3" fill="none" stroke="#fff" stroke-width="3"/><circle cx="43" cy="20" r="2" fill="#fff"/></svg>
    <span>Virtual Office<br>Solutions</span>
  </div>
  <div class="service" style="left:965px">
    <svg width="60" height="52" viewBox="0 0 60 52"><circle cx="18" cy="22" r="8" fill="#fff"/><path d="M4 50c0-14 6-20 14-20s14 6 14 20z" fill="#fff"/><rect x="30" y="3" width="26" height="20" fill="none" stroke="#fff" stroke-width="3"/><path d="M40 9v8l6-4z" fill="#fff"/></svg>
    <span>Video Conference<br>Solutions</span>
  </div>
</section>

<h2 class="section-title abs" style="top:1404px">LATEST NEWS</h2>
<div class="title-rule abs" style="top:1452px"></div>

<div class="news-icon abs" style="left:65px;top:1491px">
  <svg width="40" height="40" viewBox="0 0 40 40"><path d="M8 32l3-10L27 6l7 7-16 16z" fill="#3a8fc7"/><path d="M8 32l3-10 7 7z" fill="#fff"/></svg>
</div>
<div class="view-btn abs" style="left:63px;top:1608px">View Now</div>
<h3 class="news-title abs" style="left:204px;top:1481px">Build Education Website Using PressKit</h3>
<div class="news-meta abs" style="left:204px;top:1530px"><span>&#9719; 8:00 AM - 5:00 PM</span><span>&#9679; CHICAGO, US</span></div>
<p class="news-body abs" style="left:204px;top:1558px">Lorem Ipsum is simply dummy text of the printing and typesetting industry. Lorem Ipsum has been the industry's standard dummy text ever since the 1500s, when an unknown printer took a galley of type and scrambled it to make a type specimen book. It has survived not only five centuries.</p>
<div class="news-photo abs" role="img" aria-label="Desk with notebooks, tablet and stationery" style="left:801px;top:1487px;background:linear-gradient(135deg,#b98a6c,#e8d7c6 45%,#a8693f)"></div>

<div class="news-divider abs"></div>

<div class="news-icon abs" style="left:65px;top:1733px">
  <svg width="40" height="40" viewBox="0 0 40 40"><path d="M8 32l3-10L27 6l7 7-16 16z" fill="#3a8fc7"/><path d="M8 32l3-10 7 7z" fill="#fff"/></svg>
</div>
<div class="view-btn abs" style="left:63px;top:1850px">View Now</div>
<h3 class="news-title abs" style="left:204px;top:1723px">Build Education Website Using PressKit</h3>
<div class="news-meta abs" style="left:204px;top:1772px"><span>&#9719; 8:00 AM - 5:00 PM</span><span>&#9679; CHICAGO, US</span></div>
<p class="news-body abs" style="left:204px;top:1800px">Lorem Ipsum is simply dummy text of the printing and typesetting industry. Lorem Ipsum has been the industry's standard dummy text ever since the 1500s, when an unknown printer took a galley of type and scrambled it to make a type specimen book. It has survived not only five centuries.</p>
<div class="news-photo abs" role="img" aria-label="Student writing at a desk" style="left:801px;top:1729px;background:linear-gradient(135deg,#f2f2f0,#d9b7a8 50%,#d46a5e)"></div>

<section class="watch abs">
  <h2 class="section-title abs" style="top:30px">WATCH HOW IT WORKS</h2>
  <div class="title-rule abs" style="top:78px"></div>
</section>
<div class="video abs" role="img" aria-label="Video still of a campus lake at sunset">
  <div class="video-title abs">Riverside Campus time-lapse - full version</div>
  <div class="play abs"><svg width="22" height="24" viewBox="0 0 22 24"><path d="M3 2l17 10-17 10z" fill="#fff"/></svg></div>
  <div class="video-bar abs">
    <svg width="12" height="14" viewBox="0 0 12 14"><rect x="1" y="1" width="3" height="12" fill="#fff"/><rect x="8" y="1" width="3" height="12" fill="#fff"/></svg>
    <svg width="16" height="14" viewBox="0 0 16 14"><path d="M1 5h4l5-4v12l-5-4H1z" fill="#fff"/></svg>
    <span>0:01 / 3:46</span>
  </div>
</div>

<section class="touch abs">
  <h2>GET IN TOUCH</h2>
  <div class="rule abs"></div>
  <p>Get the latest updates on our courses and events: Notify Me</p>
  <div class="field abs" style="left:115px;width:407px">ENTER NAME</div>
  <div class="field abs" style="left:537px;width:407px">ENTER EMAIL</div>
  <div class="subscribe abs">SUBSCRIBE</div>
</section>

<footer class="site-footer abs">
  <h4 style="left:87px">Navigation Links</h4>
  <ul class="foot-links" style="left:89px"><li>About Us</li><li>Contact Us</li><li>Forms</li><li>Testimonials</li><li>FAQs</li></ul>
  <ul class="foot-links" style="left:286px"><li>Careers</li><li>Furniture</li><li>Specials</li><li>Site Map</li><li>Privacy</li></ul>
  <h4 style="left:494px">Newsletter Letter</h4>
  <div class="news-box abs">
    <div class="lead">Sign up to our mailing list</div>
    <div class="small">Suspendisse tempus sodales neque, eget eleifend turpis tristique eu.</div>
    <div class="mail-row"><span class="mail-in">Email</span><span class="mail-btn">Subscribe</span></div>
  </div>
  <h4 style="left:879px">Social Media</h4>
  <span class="foot-social" style="left:880px;background:#3b5998"></span>
  <span class="foot-social" style="left:924px;background:#1da1f2"></span>
  <span class="foot-social" style="left:968px;background:#d9282a"></span>
  <span class="foot-social" style="left:1016px;background:#517fa4"></span>
  <span class="foot-social" style="left:1060px;background:#dd5a44"></span>
  <div class="foot-brand abs"><span class="brand-dot"></span><span class="brand-name">CALLOWAY</span></div>
</footer>
<div class="copyright abs">COPYRIGHT 2012 CALLOWAY BUSINESS CENTERS ALL RIGHTS RESERVED</div>

</body>
</html>
```